Basins And Brooks Inc. Cultured marble and solidsurface fabrication and installation builders and home

We need a postcard design for a cultured marble company in Wills Point Texas. We manufacture showers, shower pans, bath tubs, vanity sinks and solid surface kitchen counter tops. Company name is Basins and Brooks Inc. We are looking to generate sales and inform customers of what we offer. We are open to the public as well as home builders and offer standard and custom applications. New construction and remodels.

Target Market(s)

Home builders and home owners

Industry/Entity Type

Construction

Font styles to use
Serif
Sans Serif
Script

Colors
000000
85acd3
0555a3
3176b5
0692cd
33a6d7
85cae6
d0dfed

Requirements
Must have
• Name, services offered

```html
<!DOCTYPE html>
<html lang="en">
<head>
<meta charset="utf-8">
<title>Basins And Brooks Inc. Postcard</title>
<link rel="stylesheet" href="https://fonts.googleapis.com/css2?family=Open+Sans:wght@400;600;700;800&family=Roboto+Condensed:wght@700&display=swap">
<style>
  :root {
    --black: #000000;
    --ink: #0d0d0f;
    --navy: #0555a3;
    --mid-blue: #3176b5;
    --bright-blue: #0692cd;
    --sky: #33a6d7;
    --pale-sky: #85cae6;
    --mist: #d0dfed;
    --steel: #85acd3;
    --white: #ffffff;
    --backdrop: #e9ecef;
  }
  * { box-sizing: border-box; margin: 0; padding: 0; }
  html, body { width: 796px; height: 1200px; overflow: hidden; }
  body {
    background: var(--backdrop);
    font-family: "Open Sans", Arial, sans-serif;
    position: relative;
  }
  .postcard {
    position: absolute;
    left: 58px;
    width: 680px;
    height: 490px;
    overflow: hidden;
    box-shadow: 0 4px 14px rgba(0,0,0,.25);
  }
  .postcard--front { top: 40px; background: var(--ink); }
  .postcard--back { top: 630px; background: var(--white); }
  .card-art { position: absolute; inset: 0; width: 100%; height: 100%; }

  /* front */
  .brand-title {
    position: absolute; right: 22px; top: 20px; width: 280px;
    text-align: left; color: var(--white);
    font-family: "Roboto Condensed", "Arial Narrow", sans-serif;
    text-transform: uppercase; line-height: 1.15;
  }
  .brand-title .company { font-size: 26px; letter-spacing: .5px; }
  .brand-title .material { font-size: 29px; color: var(--sky); }
  .brand-title .surface { font-size: 24px; }
  .manufacture-bar {
    position: absolute; left: 404px; right: 0; top: 168px; height: 42px;
    background: var(--bright-blue); color: var(--white);
    font-family: "Roboto Condensed", "Arial Narrow", sans-serif;
    font-size: 24px; padding: 6px 0 0 22px; text-transform: uppercase;
  }
  .product-list {
    position: absolute; left: 458px; top: 226px; list-style: none;
    color: var(--navy); font-weight: 700; font-size: 15px; line-height: 24px;
  }
  .product-list li { position: relative; padding-left: 18px; }
  .product-list li::before {
    content: ""; position: absolute; left: 0; top: 9px;
    width: 7px; height: 7px; border-radius: 50%; background: var(--bright-blue);
  }
  .product-list .wrap { padding-left: 18px; }
  .badge { position: absolute; left: 300px; top: 318px; width: 150px; height: 150px; }
  .badge-text {
    position: absolute; left: 300px; top: 352px; width: 150px; text-align: center;
    color: var(--navy); font-family: "Roboto Condensed", "Arial Narrow", sans-serif;
    text-transform: uppercase; line-height: 1;
  }
  .badge-text .big { font-size: 26px; display: block; }
  .badge-text .small { font-size: 12px; display: block; margin-top: 4px; }
  .contact {
    position: absolute; list-style: none; color: var(--white); font-size: 14px; line-height: 24px;
  }
  .contact li { display: flex; align-items: center; gap: 8px; }
  .contact svg { width: 13px; height: 13px; flex: none; }
  .contact--front { left: 26px; top: 380px; }

  /* back */
  .about-label {
    position: absolute; left: 0; top: 196px; width: 176px; height: 26px;
    background: var(--ink); color: var(--white); font-weight: 800;
    font-size: 16px; padding: 2px 0 0 26px; text-transform: uppercase;
  }
  .about-copy {
    position: absolute; left: 26px; top: 232px; width: 262px;
    color: var(--white); font-size: 12.5px; line-height: 15.5px;
  }
  .about-copy .name { color: var(--ink); font-weight: 700; }
  .call-line {
    position: absolute; left: 26px; top: 362px; color: var(--ink);
    font-weight: 800; font-size: 25px;
  }
  .call-line span { color: var(--navy); }
  .contact--back { left: 26px; top: 416px; font-size: 13px; line-height: 22px; }
  .stamp-box {
    position: absolute; right: 22px; top: 24px; width: 72px; height: 84px;
    border: 2px solid #9aa3ab;
  }
  .address-lines { position: absolute; left: 378px; top: 250px; width: 280px; }
  .address-lines span { display: block; height: 1px; background: #b6bcc2; margin-bottom: 34px; }
</style>
</head>
<body>

<section class="postcard postcard--front" aria-label="Postcard front">
  <svg class="card-art" viewBox="0 0 680 490" aria-hidden="true">
    <defs>
      <linearGradient id="bathPhoto" x1="0" y1="0" x2="1" y2="1">
        <stop offset="0" stop-color="#cfd6d8"/>
        <stop offset=".5" stop-color="#e8e4dc"/>
        <stop offset="1" stop-color="#9b9388"/>
      </linearGradient>
      <linearGradient id="blueSweep" x1="0" y1="0" x2="1" y2="0">
        <stop offset="0" stop-color="#0555a3"/>
        <stop offset="1" stop-color="#33a6d7"/>
      </linearGradient>
    </defs>
    <path d="M0 0 H400 V250 C300 270 170 300 0 330 Z" fill="url(#bathPhoto)"/>
    <path d="M0 330 C170 300 300 270 400 250 L400 268 C300 292 170 322 0 356 Z" fill="url(#blueSweep)"/>
    <path d="M0 356 C170 322 300 292 400 268 L400 278 C300 304 170 334 0 368 Z" fill="#ffffff"/>
    <rect x="404" y="210" width="276" height="210" fill="#ffffff"/>
    <path d="M404 420 H680 V490 H470 C520 470 560 445 580 420 Z" fill="#0d0d0f"/>
    <path d="M560 490 C610 460 650 440 680 430 V490 Z" fill="#0692cd"/>
  </svg>
  <div role="img" aria-label="Photo of a bathroom with a cultured marble tub beneath a window" style="position:absolute;left:0;top:0;width:400px;height:250px;"></div>

  <h1 class="brand-title">
    <span class="company">Basins And Brooks Inc</span><br>
    <span class="material">Cultered Marble</span><br>
    <span class="surface">And Solid Surface</span>
  </h1>

  <div class="manufacture-bar">We Manufacture</div>
  <ul class="product-list">
    <li>Showers</li>
    <li>Shower pans</li>
    <li>Bath tubs</li>
    <li>Vanity sinks</li>
    <li class="wrap" style="padding-left:18px">and solid surface</li>
    <li>kitchen counter tops</li>
  </ul>

  <svg class="badge" viewBox="-75 -75 150 150" aria-hidden="true">
    <polygon fill="#33a6d7" points="72,0 61.8,16.6 62.4,36 45.3,45.3 36,62.4 16.6,61.8 0,72 -16.6,61.8 -36,62.4 -45.3,45.3 -62.4,36 -61.8,16.6 -72,0 -61.8,-16.6 -62.4,-36 -45.3,-45.3 -36,-62.4 -16.6,-61.8 0,-72 16.6,-61.8 36,-62.4 45.3,-45.3 62.4,-36 61.8,-16.6"/>
    <circle r="57" fill="#85cae6" stroke="#ffffff" stroke-width="3"/>
  </svg>
  <div class="badge-text">
    <span class="big">Custom</span>
    <span class="big">Homes</span>
    <span class="small">And Remodels</span>
  </div>

  <ul class="contact contact--front">
    <li><svg viewBox="0 0 16 16"><path fill="#33a6d7" d="M3 1 L6 1 L7 5 L5 6.5 C6 9 7 10 9.5 11 L11 9 L15 10 L15 13 C15 14 14 15 13 15 C6 15 1 10 1 3 C1 2 2 1 3 1Z"/></svg>9035550142</li>
    <li><svg viewBox="0 0 16 16"><circle cx="8" cy="8" r="6.5" fill="none" stroke="#33a6d7" stroke-width="2"/><circle cx="8" cy="8" r="2.5" fill="#33a6d7"/></svg>9035550187</li>
    <li><svg viewBox="0 0 16 16"><rect x="1" y="3" width="14" height="10" fill="none" stroke="#33a6d7" stroke-width="2"/><path d="M1 3 L8 9 L15 3" fill="none" stroke="#33a6d7" stroke-width="2"/></svg>hello@basinsbrooks.net</li>
    <li><svg viewBox="0 0 16 16"><circle cx="8" cy="8" r="6.5" fill="none" stroke="#33a6d7" stroke-width="2"/><path d="M1.5 8 H14.5 M8 1.5 C5 5 5 11 8 14.5 M8 1.5 C11 5 11 11 8 14.5" fill="none" stroke="#33a6d7" stroke-width="1.4"/></svg>www.basinsandbrooksinc.com</li>
  </ul>
</section>

<section class="postcard postcard--back" aria-label="Postcard back">
  <svg class="card-art" viewBox="0 0 680 490" aria-hidden="true">
    <defs>
      <linearGradient id="aboutBlue" x1="0" y1="0" x2="0" y2="1">
        <stop offset="0" stop-color="#33a6d7"/>
        <stop offset="1" stop-color="#0692cd"/>
      </linearGradient>
      <linearGradient id="vanityPhoto" x1="0" y1="0" x2="1" y2="1">
        <stop offset="0" stop-color="#d8d2c6"/>
        <stop offset="1" stop-color="#8e8678"/>
      </linearGradient>
    </defs>
    <path d="M0 0 H310 V150 H0 Z" fill="#0d0d0f"/>
    <path d="M0 130 C80 90 210 70 310 100 V150 H0 Z" fill="#3176b5"/>
    <path d="M0 140 C120 110 260 110 330 180 C360 260 345 360 300 420 H0 Z" fill="url(#aboutBlue)"/>
    <path d="M0 420 H300 C320 400 335 380 340 360 V490 H0 Z" fill="#0d0d0f"/>
    <circle cx="250" cy="76" r="58" fill="#ffffff"/>
    <circle cx="250" cy="76" r="52" fill="url(#vanityPhoto)"/>
  </svg>
  <div role="img" aria-label="Photo of a cultured marble vanity sink" style="position:absolute;left:198px;top:24px;width:104px;height:104px;border-radius:50%;"></div>

  <div class="about-label">About Us</div>
  <p class="about-copy"><span class="name">Basins And Brooks Inc.</span> Has been providing the finest quality cultured marble products to the East Texas and Dallas areas for Thirty years. Now we are proud to offer solidsurface for the kitchen and bath. Our promise to you is a fair price for a finely crafted product.</p>
  <p class="call-line">Call us <span>9035550142</span></p>

  <ul class="contact contact--back">
    <li><svg viewBox="0 0 16 16"><circle cx="8" cy="8" r="6.5" fill="none" stroke="#33a6d7" stroke-width="2"/><circle cx="8" cy="8" r="2.5" fill="#33a6d7"/></svg>9035550187</li>
    <li><svg viewBox="0 0 16 16"><rect x="1" y="3" width="14" height="10" fill="none" stroke="#33a6d7" stroke-width="2"/><path d="M1 3 L8 9 L15 3" fill="none" stroke="#33a6d7" stroke-width="2"/></svg>hello@basinsbrooks.net</li>
    <li><svg viewBox="0 0 16 16"><circle cx="8" cy="8" r="6.5" fill="none" stroke="#33a6d7" stroke-width="2"/><path d="M1.5 8 H14.5 M8 1.5 C5 5 5 11 8 14.5 M8 1.5 C11 5 11 11 8 14.5" fill="none" stroke="#33a6d7" stroke-width="1.4"/></svg>www.basinsandbrooksinc.com</li>
  </ul>

  <div class="stamp-box"></div>
  <div class="address-lines"><span></span><span></span><span></span><span></span></div>
</section>

</body>
</html>
```